Upstart Retirement Planning Firm needs help with business card design

Harborview Nest Advisors, LLC is looking for help with business card design. We give advice on investments, insurance, and other financial matters related to retirement. There are some required disclosures that we will provide but mostly we are looking for a professional, classy business card that reflects the theme we have chosen. We have a logo that is attached but we would like to add a phrase; "Turning Your Earned Income Into Retirement Income"

Doubled sided only so that we can add the required disclosures (needed for our industry) on the back of the card. We will provide the exact words for this in 1-2 days.

Target Market(s)

Retirees and Pre-retirees. Professionals 50+ years old

Industry/Entity Type

Financial Planning

Contact Information for Business Card

We currently have two people who will need separate cards so we'd like to have a template so that we can add names for new cards in the future.

For the first run, please show the following information.

Gregor Pelham, MBA, ChFC®, CLU®
Financial Advisor, Registered Representative
gpelham@harborviewnest.example
Phone: (555) 318-2946
Toll Free Fax: (800) 555-0193

Address is
2187 Meadowlark Ridge Rd.
Suite K418
Virginia Beach, VA 23999

Colors
3277b5

Requirements
Must have
• Logo, contact info, small phase to describe business (in description), required legal disclosures on back of the card as follows (in small font)
• Gregor Pelham is a registered representative of and offers securities through Brightmoor Capital Brokerage Corporation, Member FNQX. Brightmoor Capital Brokerage Corporation is a member of the Brightmoor Capital Alliance which is the marketing name for Brightmoor Holding Corporation and its affiliates.
Nice to have
• Rounded edges, raised letters
Should not have
• any colors that aren't in the logo (other than black for font)

```html
<!DOCTYPE html>
<html lang="en">
<head>
<meta charset="utf-8">
<title>Harborview Nest Advisors – Business Cards</title>
<link rel="stylesheet" href="https://fonts.googleapis.com/css2?family=Source+Sans+3:wght@400;600;700&display=swap">
<style>
  :root {
    --brand-blue: #2e5b9f;
    --band-grey: #a3a6aa;
    --paper: #ffffff;
    --paper-shade: #f1f2f4;
    --ink-grey: #4a4d52;
    --canvas-bg: #e9e6e1;
  }
  * { box-sizing: border-box; margin: 0; padding: 0; }
  html, body {
    width: 1200px; height: 900px; overflow: hidden;
    background: var(--canvas-bg);
    font-family: "Source Sans 3", "Myriad Pro", Arial, sans-serif;
  }
  .canvas { position: relative; width: 1200px; height: 900px; }

  .card {
    position: absolute;
    width: 560px; height: 320px;
    border-radius: 10px;
    overflow: hidden;
    box-shadow: 0 6px 18px rgba(0,0,0,0.18);
  }

  /* Front */
  .card--front {
    left: 90px; top: 110px;
    background: var(--brand-blue);
    display: flex; align-items: center; justify-content: center;
  }
  .brand {
    display: flex; flex-direction: column; align-items: center; gap: 10px;
  }
  .brand__mark {
    width: 18px; height: 18px; border-radius: 50%;
    background: currentColor;
  }
  .brand__name {
    font-weight: 600; font-size: 24px; letter-spacing: 2.5px;
    text-transform: uppercase; text-align: center;
  }
  .brand__rule { width: 300px; height: 1px; background: currentColor; opacity: 0.6; }
  .card--front .brand { color: var(--paper); }

  /* Back */
  .card--back {
    left: 550px; top: 470px;
    background: var(--brand-blue);
  }
  .card__top {
    position: absolute; left: 0; top: 0; width: 100%; height: 170px;
    background: linear-gradient(180deg, var(--paper) 0%, var(--paper-shade) 100%);
  }
  .card__band {
    position: absolute; left: 0; top: 170px; width: 100%; height: 10px;
    background: var(--band-grey);
  }
  .card--back .brand {
    position: absolute; left: 150px; top: 28px; width: 360px;
    color: var(--brand-blue); gap: 8px;
  }
  .card--back .brand__name { font-size: 18px; letter-spacing: 2px; }
  .card--back .brand__rule { width: 260px; }

  .contact-top {
    position: absolute; right: 26px; top: 112px;
    text-align: right; color: var(--ink-grey); font-size: 14px; line-height: 24px;
  }
  .contact-line { display: flex; align-items: center; justify-content: flex-end; gap: 6px; }
  .contact-line svg { width: 12px; height: 12px; fill: var(--ink-grey); }

  .advisor {
    position: absolute; left: 26px; top: 192px; color: var(--paper);
  }
  .advisor__name { font-weight: 700; font-size: 22px; line-height: 26px; }
  .advisor__creds { font-weight: 600; font-size: 15px; }
  .advisor__title { font-size: 15px; line-height: 22px; }

  .address {
    position: absolute; left: 26px; top: 258px; color: var(--paper);
    font-size: 15px; line-height: 22px;
  }
  .fax {
    position: absolute; right: 26px; top: 196px; color: var(--paper);
    font-weight: 700; font-size: 14px;
  }
</style>
</head>
<body>
<main class="canvas">

  <section class="card card--front" aria-label="Business card front">
    <div class="brand">
      <span class="brand__mark"></span>
      <span class="brand__name">Harborview Nest Advisors, LLC</span>
      <span class="brand__rule"></span>
    </div>
  </section>

  <section class="card card--back" aria-label="Business card back">
    <div class="card__top"></div>
    <div class="card__band"></div>

    <div class="brand">
      <span class="brand__mark"></span>
      <span class="brand__name">Harborview Nest Advisors, LLC</span>
      <span class="brand__rule"></span>
    </div>

    <div class="contact-top">
      <div class="contact-line">(555) 318-2946
        <svg viewBox="0 0 24 24" aria-hidden="true"><path d="M6.6 10.8a15.1 15.1 0 0 0 6.6 6.6l2.2-2.2a1 1 0 0 1 1-.25 11.4 11.4 0 0 0 3.6.57 1 1 0 0 1 1 1V20a1 1 0 0 1-1 1A17 17 0 0 1 3 4a1 1 0 0 1 1-1h3.5a1 1 0 0 1 1 1c0 1.25.2 2.45.57 3.57a1 1 0 0 1-.25 1z"/></svg>
      </div>
      <div class="contact-line">gpelham@harborviewnest.example
        <svg viewBox="0 0 24 24" aria-hidden="true"><path d="M2 5h20v14H2z M4 7v.5l8 5 8-5V7l-8 5z" fill-rule="evenodd"/></svg>
      </div>
    </div>

    <div class="advisor">
      <div class="advisor__name">Gregor Pelham, MBA, <span class="advisor__creds">ChFC®, CLU®</span></div>
      <div class="advisor__title">Financial Advisor, Registered Representative</div>
    </div>

    <div class="fax">Toll Free Fax: (800) 555-0193</div>

    <div class="address">
      2187 Meadowlark Ridge Rd. Suite<br>
      K418 Virginia Beach, VA 23999
    </div>
  </section>

</main>
</body>
</html>
```